Irrigation Business needs their business cards modernised and revamped

I would like to keep my current logo, colours and revamp the format of the card.

I would like the card to be clean yet important.

Im not sure if you include texture but i would like the named logo to be indented into the card etc.

show me something alive and free something thats clinical to the point yet has a feel of achievement. i would like people to go nice card.

Target Market(s)

high end clients, corporate, sports field manger, the guys that make the decisions

Industry/Entity Type

Business

Contact Information for Business Card

nformation to be included

Dean Harlow (Director)
0487305526
dean@kolvat.biz
www.kestonfieldworks.com

instagram logo
google logo
facebook logo

Colors

Designer to choose colors to be used in the design.

Requirements
Nice to have
• indentations a really nice feel to the card good texture

```html
<!DOCTYPE html>
<html lang="en">
<head>
<meta charset="utf-8">
<title>Keston Fieldworks – Business Card</title>
<link href="https://fonts.googleapis.com/css2?family=Roboto+Condensed:wght@700&family=Open+Sans:wght@400;600&display=swap" rel="stylesheet">
<style>
  :root {
    --backdrop: #2a2a2b;
    --card: #202122;
    --card-edge: #2c2d2e;
    --brand-blue: #2f7fd0;
    --brand-green: #36b36a;
    --sky: #47b6e6;
    --text-light: #f1f3f5;
    --rule: #8a8d90;
  }
  * { box-sizing: border-box; margin: 0; padding: 0; }
  html, body {
    width: 1200px; height: 900px; overflow: hidden;
    background: var(--backdrop);
  }
  .stage {
    position: relative; width: 1200px; height: 900px;
    display: flex; flex-direction: column; align-items: center; justify-content: center; gap: 50px;
  }
  .card {
    position: relative; width: 630px; height: 360px;
    background: var(--card);
    border: 1px solid var(--card-edge);
    border-radius: 4px;
    box-shadow: 0 14px 30px rgba(0,0,0,.45);
  }

  /* Front */
  .card--front .brand {
    position: absolute; top: 70px; left: 0; right: 0;
    display: flex; flex-direction: column; align-items: center; gap: 18px;
  }
  .brand__dot {
    width: 84px; height: 84px; border-radius: 50%;
    background: var(--sky);
  }
  .brand__name {
    font-family: "Roboto Condensed", "Arial Narrow", sans-serif;
    font-weight: 700; font-size: 36px; letter-spacing: 1px;
    color: var(--brand-blue); text-transform: uppercase;
  }
  .card--front .social-rule {
    position: absolute; left: 40px; right: 40px; top: 262px;
    display: flex; align-items: center; gap: 8px;
  }
  .social-rule__line {
    flex: 1; height: 1px;
  }
  .social-rule__line--left { background: linear-gradient(to right, transparent, var(--rule)); }
  .social-rule__line--right { background: linear-gradient(to left, transparent, var(--rule)); }
  .social-rule__badge {
    width: 28px; height: 28px; border-radius: 50%;
    background: var(--brand-blue);
  }

  /* Back */
  .card--back .identity {
    position: absolute; right: 345px; top: 140px; text-align: right;
  }
  .identity__name {
    font-family: "Roboto Condensed", "Arial Narrow", sans-serif;
    font-weight: 700; font-size: 34px; color: var(--brand-blue);
    text-transform: uppercase; letter-spacing: .5px;
  }
  .identity__role {
    font-family: "Open Sans", Arial, sans-serif;
    font-weight: 600; font-size: 17px; color: var(--brand-green);
    text-transform: uppercase; letter-spacing: .5px; margin-top: 2px;
  }
  .card--back .divider {
    position: absolute; left: 305px; top: 120px; width: 2px; height: 100px;
    background: linear-gradient(to bottom, transparent, var(--rule), transparent);
  }
  .contact-list {
    position: absolute; left: 330px; top: 140px; list-style: none;
    display: flex; flex-direction: column; gap: 7px;
  }
  .contact-list__item {
    display: flex; align-items: center; gap: 10px;
    font-family: "Open Sans", Arial, sans-serif; font-size: 16px; color: var(--text-light);
  }
  .contact-list__icon { width: 14px; height: 14px; fill: var(--brand-blue); flex: none; }
</style>
</head>
<body>
<main class="stage">
  <section class="card card--front" aria-label="Card front">
    <div class="brand">
      <span class="brand__dot"></span>
      <span class="brand__name">Keston Fieldworks</span>
    </div>
    <div class="social-rule">
      <span class="social-rule__line social-rule__line--left"></span>
      <span class="social-rule__badge" aria-label="Social profile"></span>
      <span class="social-rule__badge" aria-label="Social profile"></span>
      <span class="social-rule__badge" aria-label="Social profile"></span>
      <span class="social-rule__line social-rule__line--right"></span>
    </div>
  </section>

  <section class="card card--back" aria-label="Card back">
    <div class="identity">
      <p class="identity__name">Dean Harlow</p>
      <p class="identity__role">Director</p>
    </div>
    <span class="divider"></span>
    <ul class="contact-list">
      <li class="contact-list__item">
        <svg class="contact-list__icon" viewBox="0 0 24 24"><path d="M6.6 10.8a15.2 15.2 0 0 0 6.6 6.6l2.2-2.2c.3-.3.7-.4 1-.2 1.1.4 2.3.6 3.6.6.6 0 1 .4 1 1V20c0 .6-.4 1-1 1A17 17 0 0 1 3 4c0-.6.4-1 1-1h3.5c.6 0 1 .4 1 1 0 1.3.2 2.5.6 3.6.1.3 0 .7-.2 1z"/></svg>
        <span>0487305526</span>
      </li>
      <li class="contact-list__item">
        <svg class="contact-list__icon" viewBox="0 0 24 24"><path d="M2 5h20v14H2z M2 5l10 7 10-7" fill="none" stroke="currentColor"/><path d="M2 5h20v2l-10 7L2 7z M2 9l10 7 10-7v10H2z"/></svg>
        <span>dean@kolvat.biz</span>
      </li>
      <li class="contact-list__item">
        <svg class="contact-list__icon" viewBox="0 0 24 24"><circle cx="12" cy="12" r="10"/><path d="M2 12h20M12 2c3 3 3 17 0 20M12 2c-3 3-3 17 0 20" fill="none" stroke="#202122" stroke-width="1.5"/></svg>
        <span>www.kestonfieldworks.com</span>
      </li>
    </ul>
  </section>
</main>
</body>
</html>
```